Meridian Vault Data Works Needs a Website Desing

We need a website design for a new company based in Kuwait called Meridian Vault Data Works (MVDW). We provide Software as a Service (SaaS) solutions for small and medium business companies. We will develop the required E-systems like HR,Payroll,Accounting Systems for those customers who wants to focus on their business instead of wasting time to automate it. MVDW need a web site that represent this activity and showing our cloud products and allow out customers to easily identify their needs. as a normal web site basic things need to be included like :
about MVDW
Solutions
PressRoom
Contact us
please i need something similar to tralvex.com or ozk.com or www.plorvane.com with blue and black theme .. please check the Company's logo
hi all ,,,
the project is only design without any codes
Reason: The project is focus on design only ,, i will be really appreciated to have more designs

```html
<!DOCTYPE html>
<html lang="en">
<head>
<meta charset="utf-8">
<title>Meridian Vault Data Works</title>
<link href="https://fonts.googleapis.com/css2?family=Arimo:wght@400;700&display=swap" rel="stylesheet">
<style>
:root{
  --blue:#0a84c6;
  --blue-dark:#0567a6;
  --ink:#222;
  --text:#555;
  --muted:#666;
  --nav-top:#5b5b5b;
  --nav-bot:#2e2e2e;
  --panel:#ffffff;
  --line:#c9cfd2;
  --box:#f4f4f4;
}
*{box-sizing:border-box;margin:0;padding:0}
html,body{width:1120px;height:1200px;overflow:hidden}
body{
  font-family:"Arimo",Arial,sans-serif;
  background:linear-gradient(#f3f6f7 0,#e6edf0 500px,#d9e5e9 1200px);
  position:relative;color:var(--text);
}
.abs{position:absolute}
.topbar{left:0;top:0;width:1120px;height:6px;background:#555}

/* header */
.brand{left:84px;top:21px;display:flex;align-items:center;gap:8px}
.brand-mark{width:62px;height:62px;border-radius:50%;background:var(--blue)}
.brand-name{color:var(--ink);font-weight:700;line-height:1}
.brand-name .short{display:block;font-size:44px;letter-spacing:1px}
.brand-name .long{display:block;font-size:10px;margin-top:3px}
.account{left:674px;top:46px;font-size:13px;font-weight:700;color:var(--blue)}
.account span{margin:0 12px;color:var(--blue)}
.search{left:830px;top:38px;width:205px;height:32px;border:1px solid #cfd3d5;background:#fff;font-size:11px;color:#333;padding:9px 14px}
.search svg{position:absolute;right:8px;top:7px}

/* nav */
.nav{left:84px;top:104px;width:952px;height:51px;background:linear-gradient(var(--nav-top),var(--nav-bot));border-radius:3px 3px 0 0;display:flex;align-items:center}
.nav a{height:51px;display:flex;align-items:center;justify-content:center;color:#fff;font-size:13px;font-weight:700;text-decoration:none;border-right:1px solid #222;box-shadow:1px 0 0 #666}
.nav a.active{background:linear-gradient(#1a94d6,#066aa9)}
.nav .call{margin-left:auto;padding-right:20px;color:#fff;font-size:16px;font-weight:700}

/* main panel */
.panel{left:84px;top:155px;width:952px;height:772px;background:var(--panel);border:1px solid #e1e5e7}

.slider{left:93px;top:162px;width:935px;height:311px;background:#dfe3e5;padding:6px 7px}
.slide-art{position:absolute;left:6px;top:6px;width:921px;height:297px;background:linear-gradient(110deg,#dfeeff 0,#7eaaf0 18%,#3d74de 40%,#3a6ce0 65%,#5d8be8 100%)}
.slide-copy{left:510px;top:226px;width:470px;color:#fff}
.slide-copy h2{font-size:19px;line-height:24px;font-weight:700;margin-bottom:10px;white-space:nowrap}
.slide-copy p{font-size:12.8px;line-height:19.5px;width:468px}
.btn-more{left:509px;top:357px;width:86px;height:29px;background:linear-gradient(#fff,#e2e2e2);border-radius:4px;font-size:11.5px;font-weight:700;color:#444;display:flex;align-items:center;justify-content:center;box-shadow:0 1px 2px rgba(0,0,0,.3)}
.dots{left:890px;top:424px;display:flex;gap:14px}
.dots i{width:17px;height:17px;border-radius:50%;background:#333;border:2px solid #fff;display:block}
.dots i.on{background:transparent;border-color:#fff;box-shadow:inset 0 0 0 1px #1593d8}

.welcome{left:94px;top:494px;width:660px}
.welcome h1{font-size:20px;color:var(--blue);font-weight:700;margin-bottom:10px}
.welcome .lead{color:var(--blue);font-size:12.2px;line-height:22px;margin-bottom:8px}
.welcome .body{font-size:12.3px;line-height:21.5px;text-align:justify}

.press{left:774px;top:496px;width:255px;height:182px;background:linear-gradient(#2e9ee0,#0a77bf);border-radius:3px;padding:42px 5px 5px}
.press-head{position:absolute;left:10px;top:10px;display:flex;align-items:center;gap:8px;color:#fff;font-size:18px;font-weight:700}
.press-head i{width:22px;height:20px;background:#dfe9f1;display:block}
.press-arrows{position:absolute;right:12px;top:16px}
.press-card{background:#fff;height:135px;padding:10px 12px;border-radius:2px}
.press-card h3{font-size:13px;color:var(--blue);font-weight:400;margin-bottom:6px}
.press-card h3 b{margin-right:6px}
.press-card p{font-size:11.5px;line-height:18px;color:var(--muted);padding-left:17px;text-align:justify}
.press-card .date{font-size:12px;color:#222;padding-left:19px;margin-top:6px}

.divider{left:180px;top:704px;width:760px;height:1px;background:linear-gradient(90deg,transparent,#dde2e4,transparent)}

.service{top:730px;width:295px;height:180px;background:var(--box);border:2px solid #ececec;padding:10px 14px}
.service-art{position:absolute;left:16px;top:8px;width:62px;height:60px;border-radius:6px}
.service h3{margin-left:84px;margin-top:14px;font-size:14.5px;line-height:22px;color:var(--blue);font-weight:700}
.service p{font-size:12.5px;line-height:20px;margin-top:14px;text-align:justify;color:var(--muted)}
.service .more{font-size:11px;color:var(--blue);margin-top:10px}

.quick-title{left:94px;top:941px;font-size:15px;color:var(--blue)}
.rule{left:93px;width:935px;height:1px;background:#9aa3a6}
.links{top:987px;list-style:none;font-size:12px;line-height:23.5px;color:#444}
.links li::before{content:"•";margin-right:6px;color:#666}

.foot-nav{left:84px;top:1136px;font-size:12px;color:#222}
.foot-nav span{margin:0 8px}
.copy{left:84px;top:1165px;font-size:12px;color:#222}
.social{top:1146px;height:23px;padding:0 5px;border-radius:3px;color:#fff;font-size:10px;font-weight:700;display:flex;align-items:center}
</style>
</head>
<body>
<div class="abs topbar"></div>

<header>
  <div class="abs brand">
    <div class="brand-mark"></div>
    <div class="brand-name"><span class="short">MVDW</span><span class="long">Meridian Vault Data Works</span></div>
  </div>
  <div class="abs account">REGISTER<span>|</span>LOGIN</div>
  <div class="abs search">Search
    <svg width="17" height="17" viewBox="0 0 17 17"><circle cx="6.5" cy="6.5" r="4.5" fill="none" stroke="#333" stroke-width="2.4"/><line x1="10" y1="10" x2="15" y2="15" stroke="#333" stroke-width="3" stroke-linecap="round"/></svg>
  </div>
  <nav class="abs nav">
    <a class="active" style="width:94px">HOME</a>
    <a style="width:140px">ABOUT MVDW</a>
    <a style="width:127px">SOLUTIONS</a>
    <a style="width:136px">PRESSROOM</a>
    <a style="width:138px">CONTACT US</a>
    <div class="call">Call us : 555 014 2290</div>
  </nav>
</header>

<main>
  <div class="abs panel"></div>

  <section class="abs slider">
    <div class="slide-art" role="img" aria-label="Blue illustration of a computer monitor with floating data panels"></div>
  </section>
  <div class="abs slide-copy">
    <h2>We are cloud computing company providing SaaS</h2>
    <p>Aenean id lectus in nisi volutpat mollis sit amet et diam. Vestibulum eget orci vel tellus molestie rutrum a sed tortor. Quisque euismod, purus vitae accumsan cursus, mi magna fermentum urna, quis feugiat sem velit at quam. Vestibulum scelerisque velit nec mauris lacinia aliquet.</p>
  </div>
  <div class="abs btn-more">VIEW MORE</div>
  <div class="abs dots"><i class="on"></i><i></i><i></i><i></i></div>

  <section class="abs welcome">
    <h1>Welcome to our site</h1>
    <p class="lead">Aliquam et lorem orci. Quisque sed neque enim, a elementum leo. Integer dolor augue, commodo vel tincidunt sit amet, volutpat eget arcu. Vestibulum velit nunc, hendrerit nec consectetur vitae, laoreet eu enim.</p>
    <p class="body">Nulla urna nulla, pretium sit amet auctor id, gravida vitae odio. Mauris at risus elit, vel sollicitudin lectus. Curabitur placerat nunc eget justo imperdiet a ornare lorem pretium. Cras volutpat malesuada ligula, at porta velit viverra at. Donec sed dolor a arcu vehicula posuere. Cras gravida libero nec erat fermentum dapibus. Vestibulum consequat, ante ut pretium hendrerit, dolor nibh blandit metus, nec posuere neque lacus eget lorem. Pellentesque accumsan mi eu ante interdum vel tristique lorem commodo. Curabitur pharetra venenatis urna.</p>
  </section>

  <aside class="abs press">
    <div class="press-head"><i></i>Press Room</div>
    <svg class="press-arrows" width="26" height="11" viewBox="0 0 26 11"><path d="M8 0L0 5.5 8 11z" fill="#222"/><path d="M18 0l8 5.5-8 5.5z" fill="#222"/></svg>
    <div class="press-card">
      <h3><b>»</b>Duis varius ultricies</h3>
      <p>Praesent eu justo eu risus elementum posuere ut id mi. Proin nisi justo, con vallis sit amet euismod nonac orci vel tellus molestie rutrum</p>
      <div class="date">April - 29 - 2013</div>
    </div>
  </aside>

  <div class="abs divider"></div>

  <article class="abs service" style="left:93px">
    <div class="service-art" role="img" aria-label="Globe with computer screens illustration" style="background:radial-gradient(circle at 40% 40%,#9fd0f5,#1f6fb8)"></div>
    <h3>Our Services<br>Nam scelerisque aliquet</h3>
    <p>Etiam eget nibhara neque. Donec in vulputate erat. Aenean ut quam vehicula lorem ullamcor per adipiscing egestas in ante.</p>
    <div class="more">VIEW MORE &nbsp;»</div>
  </article>
  <article class="abs service" style="left:414px">
    <div class="service-art" role="img" aria-label="Gear icon illustration" style="background:linear-gradient(#9a9a9a,#3c3c3c)"></div>
    <h3>Our Services<br>Mauris id ante et ipsum</h3>
    <p>Aliquam libero sem, tempus nec lobortis a, interdum non lacus. Ut vel leo eget eros imperdiet congue.</p>
    <div class="more">VIEW MORE &nbsp;»</div>
  </article>
  <article class="abs service" style="left:734px">
    <div class="service-art" role="img" aria-label="Wrench and screwdriver tools illustration" style="background:radial-gradient(circle at 45% 45%,#cfe3f3,#5c8fbf)"></div>
    <h3>Our Services<br>Aenean erat consectetur</h3>
    <p>Nulla suscipit massa turpis, a vehicula orci. Vestibulum risus turpis, lacinia ut laoreet eu, lacinia eget sapien.</p>
    <div class="more">VIEW MORE &nbsp;»</div>
  </article>
</main>

<footer>
  <div class="abs quick-title">Quick Links</div>
  <div class="abs rule" style="top:972px"></div>
  <ul class="abs links" style="left:95px"><li>Integer lobortis</li><li>Curabitur ac</li><li>Phasellus tellus nisl</li><li>Aenean fringilla</li><li>Vestibulum</li></ul>
  <ul class="abs links" style="left:257px"><li>Integer lobortis</li><li>Curabitur ac</li><li>Phasellus tellus nisl</li><li>Aenean fringilla</li><li>Vestibulum</li></ul>
  <ul class="abs links" style="left:425px"><li>Integer lobortis</li><li>Curabitur ac</li><li>Phasellus tellus nisl</li><li>Aenean fringilla</li><li>Vestibulum</li></ul>
  <ul class="abs links" style="left:588px"><li>Integer lobortis</li><li>Curabitur ac</li><li>Phasellus tellus nisl</li><li>Aenean fringilla</li><li>Vestibulum</li></ul>
  <ul class="abs links" style="left:751px"><li>Integer lobortis</li><li>Curabitur ac</li><li>Phasellus tellus nisl</li><li>Aenean fringilla</li><li>Vestibulum</li></ul>
  <ul class="abs links" style="left:914px"><li>Integer lobortis</li><li>Curabitur ac</li><li>Phasellus tellus nisl</li><li>Aenean fringilla</li><li>Vestibulum</li></ul>
  <div class="abs rule" style="top:1115px"></div>

  <div class="abs foot-nav">Home<span>|</span>About MVDW<span>|</span>Solutions<span>|</span>PressRoom<span>|</span>Contact us</div>
  <div class="abs copy">Copyright &nbsp;©&nbsp; 2013 &nbsp;&nbsp; www.mvdw-cloud.net &nbsp;&nbsp;All rights reserved</div>
  <div class="abs social" style="left:925px;background:#3b5a9a">Friendsly</div>
  <div class="abs social" style="left:985px;background:#3aa9e0">Chirper</div>
</footer>
</body>
</html>
```